Vosley Insurance Stationery Design Project

We need a stationery design for business cards, letterhead and envelopes.

Please refer to attached brief for further information.

Industry/Entity Type

Business

```html
<!DOCTYPE html>
<html lang="en">
<head>
<meta charset="utf-8">
<title>Vosley Insurance Stationery</title>
<link href="https://fonts.googleapis.com/css2?family=Source+Sans+3:wght@400;600;700&display=swap" rel="stylesheet">
<style>
:root{
  --board:#a67f2e;
  --paper:#ffffff;
  --navy:#1b3b55;
  --blue:#1c5f8f;
  --ink:#2a2a2a;
  --grey:#8d9296;
  --faint:#e1e4e7;
  --orange:#f07a2a;
  --rule:#555;
}
*{box-sizing:border-box;margin:0;padding:0}
html,body{width:1200px;height:593px;overflow:hidden}
body{background:var(--board);font-family:"Source Sans 3",Arial,sans-serif;color:var(--ink);position:relative}
.sheet{position:absolute;background:var(--paper);box-shadow:0 1px 3px rgba(0,0,0,.25)}
.brand{position:absolute;display:flex;align-items:center;gap:6px}
.brand-dot{width:10px;height:10px;border-radius:50%;background:var(--blue)}
.brand-name{font-weight:600;color:var(--grey);line-height:1}
.tagline{position:absolute;background:var(--blue);color:#fff;font-weight:700;white-space:nowrap}
.watermark{position:absolute;display:flex;align-items:center;gap:14px}
.watermark-dot{border-radius:50%;background:var(--faint)}
.watermark-name{font-weight:600;color:var(--faint);line-height:1}
.small{font-size:5.5px;line-height:1.45;position:absolute}
.letterhead{left:24px;top:122px;width:315px;height:406px}
.fax{left:380px;top:122px;width:315px;height:406px}
.fax-title{position:absolute;left:20px;top:84px;font-size:19px;color:#111;font-weight:400}
.fax-fields{position:absolute;left:20px;top:116px;width:267px}
.fax-row{display:flex;border-bottom:1px solid var(--rule);height:17px;align-items:flex-end;font-size:5.5px;padding-bottom:2px}
.fax-row span{flex:1}
.fax-checks{position:absolute;left:20px;top:196px;display:flex;gap:12px;font-size:5.5px}
.fax-checks label{display:flex;align-items:center;gap:5px}
.box{width:7px;height:7px;border:1px solid #333}
.envelope{position:absolute}
.card{position:absolute;width:140px;height:78px}
.card-front{background:var(--paper)}
.card-mark{position:absolute;left:9px;display:flex;align-items:center;gap:3px}
.card-mark .brand-dot{background:var(--orange);width:9px;height:9px}
.card-name{color:var(--orange);font-weight:600;font-size:7px;line-height:1}
.card-url{position:absolute;left:60px;color:var(--orange);font-size:4.5px;font-weight:600;white-space:nowrap;line-height:1}
.card-legal{position:absolute;left:30px;top:52px;width:104px;text-align:center;font-size:3.2px;line-height:1.45;color:#fff}
</style>
</head>
<body>

<section class="sheet letterhead">
  <div class="brand" style="left:14px;top:16px"><span class="brand-dot"></span><span class="brand-name" style="font-size:15px">Vosley Insurance</span></div>
  <div class="tagline" style="left:13px;top:54px;font-size:6.5px;padding:1px 4px">Business and Life Insurance Brokers and Advisers</div>
  <div class="watermark" style="left:76px;top:168px"><span class="watermark-dot" style="width:34px;height:34px"></span><span class="watermark-name" style="font-size:26px">Vosley</span></div>
  <p class="small" style="left:48px;top:383px">Level 4, 18 Harbour Rd, Eastwood NSW 2122<br>PO Box 417 Eastwood NSW 2122</p>
  <p class="small" style="left:150px;top:383px;border-left:1px solid #999;padding-left:4px"><b style="color:var(--blue)">T</b> : (02) 5550 1234<br><b style="color:var(--blue)">F</b> : (02) 5550 5678</p>
  <p class="small" style="left:202px;top:383px;border-left:1px solid #999;padding-left:4px"><b style="color:var(--blue)">M</b> : 0400 555 019<br><b style="color:var(--blue)">E</b> : dwhitlow@vosley.example</p>
</section>

<section class="sheet fax">
  <div class="brand" style="left:22px;top:28px"><span class="brand-dot"></span><span class="brand-name" style="font-size:15px">Vosley Insurance</span></div>
  <p class="small" style="left:242px;top:30px"><b style="color:var(--blue)">T</b> : (02) 5550 1234<br><b style="color:var(--blue)">F</b> : (02) 5550 5678<br><b style="color:var(--blue)">M</b> : 0400 555 019<br><b style="color:var(--blue)">E</b> : dwhitlow@vosley.example</p>
  <h1 class="fax-title">FAX</h1>
  <div class="fax-fields">
    <div class="fax-row"><span>To :</span><span>From :</span></div>
    <div class="fax-row"><span>Fax :</span><span>Pages :</span></div>
    <div class="fax-row"><span>Phone :</span><span>Date :</span></div>
    <div class="fax-row"><span>Re :</span><span>CC :</span></div>
  </div>
  <div class="fax-checks">
    <label><span class="box"></span>Urgent</label>
    <label><span class="box"></span>For Review</label>
    <label><span class="box"></span>Please Comment</label>
    <label><span class="box"></span>Please Reply</label>
    <label><span class="box"></span>Please Recycle</label>
  </div>
  <div class="watermark" style="left:96px;top:254px"><span class="watermark-dot" style="width:26px;height:26px"></span><span class="watermark-name" style="font-size:22px">Vosley</span></div>
  <div class="tagline" style="left:9px;top:383px;font-size:7px;padding:2px 5px">Business and Life Insurance Brokers and Advisers</div>
  <p class="small" style="left:199px;top:383px">Level 4, 18 Harbour Rd, Eastwood NSW 2122<br>PO Box 417 Eastwood NSW 2122</p>
</section>

<svg class="envelope" style="left:770px;top:54px" width="356" height="160" viewBox="0 0 356 160">
  <rect x="0" y="0" width="356" height="158" fill="#fff"/>
  <path d="M0 0H356V26Q350 32 330 36L190 56Q178 58 166 56L26 36Q6 32 0 26Z" fill="var(--navy)"/>
  <circle cx="152" cy="20" r="6" fill="#fff"/>
  <text x="162" y="26" font-family="Source Sans 3, Arial, sans-serif" font-weight="600" font-size="14" fill="#fff">Vosley</text>
</svg>
<svg class="envelope" style="left:728px;top:120px" width="352" height="160" viewBox="0 0 352 160">
  <rect x="0" y="0" width="350" height="158" fill="#fff" stroke="#999" stroke-width="0.6"/>
  <path d="M0 0H350V10Q346 16 330 20L188 50Q175 53 162 50L20 20Q4 16 0 10Z" fill="#fff" stroke="#777" stroke-width="0.8"/>
  <circle cx="152" cy="22" r="6" fill="var(--navy)"/>
  <text x="162" y="28" font-family="Source Sans 3, Arial, sans-serif" font-weight="600" font-size="14" fill="var(--navy)">Vosley</text>
</svg>

<section class="sheet" style="left:769px;top:191px;width:353px;height:159px;box-shadow:0 0 0 .6px #999">
  <div class="brand" style="left:14px;top:12px"><span class="brand-dot"></span><span class="brand-name" style="font-size:12px">Vosley Insurance</span></div>
  <div class="tagline" style="left:13px;top:46px;font-size:6px;padding:1px 4px">Business and Life Insurance Brokers and Advisers</div>
  <p class="small" style="left:14px;top:60px">Level 4, 18 Harbour Rd, Eastwood NSW 2122<br>PO Box 417 Eastwood NSW 2122</p>
  <div class="watermark" style="left:250px;top:88px;gap:8px"><span class="watermark-dot" style="width:20px;height:20px"></span><span class="watermark-name" style="font-size:16px">Vosley</span></div>
</section>

<section class="sheet card card-front" style="left:804px;top:379px">
  <div class="brand" style="left:6px;top:6px;gap:3px"><span class="brand-dot" style="width:5px;height:5px"></span><span class="brand-name" style="font-size:7.5px">Vosley Insurance</span></div>
  <div class="tagline" style="left:6px;top:26px;font-size:3.4px;padding:1px 2px;background:#c9cdd1">Business and Life Insurance Brokers and Advisers</div>
  <p class="small" style="right:5px;top:7px;text-align:right;font-size:4px"><b style="color:var(--blue)">Dana Whitlow</b><br>Director</p>
  <p class="small" style="left:6px;top:34px;font-size:3.4px">Level 4, 18 Harbour Rd<br>Eastwood NSW 2122<br>PO Box 417<br>Eastwood NSW 2122<br><b>T</b> (02) 5550 1234<br><b>F</b> (02) 5550 5678<br><b>M</b> 0400 555 019<br><b>E</b> dwhitlow@vosley.example</p>
  <p class="small" style="right:5px;top:40px;width:72px;text-align:right;font-size:3.4px;color:#666">Authorised Representative No. 000000 of Example Advisers Pty Ltd, AFSL 000000. Members of an independent advice group.</p>
</section>
<section class="sheet card" style="left:952px;top:379px;background:var(--blue)">
  <div class="card-mark" style="top:33px"><span class="brand-dot"></span><span class="card-name">Vosley</span></div>
  <span class="card-url" style="top:36px">www.vosleyinsurance.example</span>
</section>
<section class="sheet card card-front" style="left:804px;top:464px">
  <div class="brand" style="left:6px;top:6px;gap:3px"><span class="brand-dot" style="width:5px;height:5px"></span><span class="brand-name" style="font-size:7.5px">Vosley Insurance</span></div>
  <div class="tagline" style="left:6px;top:26px;font-size:3.4px;padding:1px 2px;background:#c9cdd1">Business and Life Insurance Brokers and Advisers</div>
  <p class="small" style="left:6px;top:34px;font-size:3.4px">Level 4, 18 Harbour Rd<br>Eastwood NSW 2122<br>PO Box 417<br>Eastwood NSW 2122<br><b>T</b> (02) 5550 1234<br><b>F</b> (02) 5550 5678<br><b>M</b> 0400 555 019<br><b>E</b> dwhitlow@vosley.example</p>
  <p class="small" style="right:8px;top:56px;text-align:center;font-size:4px"><b style="color:var(--blue)">Dana Whitlow</b><br>Director</p>
</section>
<section class="sheet card" style="left:952px;top:464px;background:var(--navy)">
  <div class="card-mark" style="top:22px"><span class="brand-dot"></span><span class="card-name">Vosley</span></div>
  <span class="card-url" style="top:8px">www.vosleyinsurance.example</span>
  <p class="card-legal">Authorised Representative No. 000000 of Example Advisers Pty Ltd, AFSL 000000. Members of an independent advice group.</p>
</section>

</body>
</html>
```